Postcard Design for Birchwell Medical Center Integrated Medicine

We need a postcard that we will be able to hand out at events that gives an overview of what we do at Birchwell Medical Center. Birchwell Medical Center, located in Encinitas, California, is an integrated medical center using functional medicine to prevent and reverse chronic diseases. We would also like to highly emphasize that we take Senivex and PPO insurance for these services and if patients have any questions to contact the front desk.

The attached screenshots are elementary versions of what we hope our postcard will have.

THIS IS NOT INTENDED TO BE MAILED SO AN ADDRESS SPACE IS NOT NEEDED
ALSO, WE WOULD LIKE TO HAVE THIS SIZE 6X4

Birchwellmedicalcenter.net is our website if you would need any further information about the company.

```html
<!DOCTYPE html>
<html lang="en">
<head>
<meta charset="utf-8">
<title>Birchwell Medical Center Integrated Medicine – Postcard</title>
<link rel="stylesheet" href="https://fonts.googleapis.com/css2?family=Arimo:wght@400;700&display=swap">
<style>
  :root {
    --royal: #2a3cf0;
    --royal-deep: #1f2fd6;
    --sky-band: #4f9cf5;
    --sky-band-soft: #3f78f2;
    --lavender: #e6e6fb;
    --lavender-mid: #a9a8f3;
    --ink: #000000;
    --paper: #ffffff;
  }
  * { margin: 0; padding: 0; box-sizing: border-box; }
  html, body { width: 1200px; height: 930px; overflow: hidden; background: var(--royal); }
  .postcard {
    position: relative;
    width: 1200px;
    height: 930px;
    overflow: hidden;
    font-family: "Arimo", Arial, sans-serif;
    background: linear-gradient(180deg, var(--royal-deep) 0%, var(--royal) 50%, var(--royal-deep) 100%);
  }
  .light-band { position: absolute; top: 0; bottom: 0; }
  .band-a { left: 455px; width: 50px; background: var(--sky-band-soft); opacity: .7; }
  .band-b { left: 540px; width: 40px; background: var(--sky-band-soft); opacity: .5; }
  .band-c { left: 900px; width: 50px; background: var(--sky-band); opacity: .8; }
  .band-d { left: 1080px; width: 30px; background: var(--sky-band-soft); opacity: .6; }
  .band-e { left: 1150px; width: 50px; background: var(--sky-band); opacity: .5; }

  .emblem-area {
    position: absolute;
    left: 0; top: 0;
    width: 820px; height: 930px;
    background:
      radial-gradient(ellipse 420px 130px at 400px 70px, var(--lavender) 0%, rgba(230,230,251,.7) 55%, rgba(230,230,251,0) 100%),
      linear-gradient(90deg, rgba(169,168,243,0) 140px, rgba(169,168,243,.55) 200px, rgba(169,168,243,.55) 320px, rgba(169,168,243,0) 380px);
    background-repeat: no-repeat;
    background-size: 100% 100%, 460px 100%;
  }

  .intro {
    position: absolute;
    left: 43px; top: 52px;
    width: 860px;
    font-weight: 700;
    font-size: 27.5px;
    line-height: 38.5px;
    color: var(--ink);
    text-shadow: 0 0 2px var(--paper), 0 0 1px var(--paper);
  }
  .conditions {
    position: absolute;
    top: 255px;
    list-style: none;
    font-size: 25.5px;
    line-height: 35.8px;
    color: var(--paper);
    text-shadow:
      -1px -1px 0 var(--ink), 1px -1px 0 var(--ink),
      -1px 1px 0 var(--ink), 1px 1px 0 var(--ink),
      0 -1px 0 var(--ink), 0 1px 0 var(--ink),
      -1px 0 0 var(--ink), 1px 0 0 var(--ink);
  }
  .conditions-left { left: 38px; width: 290px; }
  .conditions-right { left: 428px; width: 420px; }

  .insurance-note {
    position: absolute;
    left: 41px; top: 656px;
    width: 600px;
    font-weight: 700;
    font-size: 26px;
    line-height: 37.5px;
    color: var(--ink);
    text-shadow: 0 0 2px var(--paper), 0 0 1px var(--paper);
  }

  .blank-panel { position: absolute; background: var(--paper); }
  .panel-top { left: 903px; top: 30px; width: 268px; height: 267px; }
  .panel-bottom { left: 151px; top: 767px; width: 1018px; height: 132px; }
</style>
</head>
<body>
  <main class="postcard" aria-label="Birchwell Medical Center Integrated Medicine postcard">
    <div class="light-band band-a"></div>
    <div class="light-band band-b"></div>
    <div class="light-band band-c"></div>
    <div class="light-band band-d"></div>
    <div class="light-band band-e"></div>

    <div class="emblem-area" role="img" aria-label="Large pale medical staff emblem with wings and entwined serpents"></div>

    <p class="intro">Treating root causes not symptoms by using a whole system approach to medicine, preventing and reversing chronic condition and disease. Ultimately, creating optimal health and vitality. Some of the conditions we treat are...</p>

    <ul class="conditions conditions-left">
      <li>Acne</li>
      <li>Diabetes</li>
      <li>Depression/Anxiety</li>
      <li>Healthy Aging</li>
      <li>Parkinson’s Disease</li>
      <li>Sleep Insomnia</li>
      <li>Healthy Weight and Metabolism</li>
      <li>Cancer Prevention</li>
      <li>Thyroid/Adrenal Disorders</li>
    </ul>
    <ul class="conditions conditions-right">
      <li>Arthritis</li>
      <li>Asthma</li>
      <li>Detoxification and Healing</li>
      <li>Migraines and Headaches</li>
      <li>Chronic Fatugue</li>
      <li>Autoimmune Diseases</li>
      <li>Food Allergies</li>
      <li>Female Disorders</li>
      <li>Hormone Imbalance</li>
      <li>Osteoporosis</li>
      <li>And many more</li>
    </ul>

    <p class="insurance-note">we accept all Senivex and PPO insurance<br>Please contact the front desk for more information</p>

    <div class="blank-panel panel-top"></div>
    <div class="blank-panel panel-bottom"></div>
  </main>
</body>
</html>
```